Business Cards for new orthopaedic surgery practice

My husband and I are starting our own orthopaedic surgery practice. We are looking for a business card that is uniform, but one will have my name/title and the other will have his. You can just create one design with my name on it for now. But when I choose your design as the winning design I will ask that you add another copy with his name/title.

We are looking for classy, simple, elite all in one. We like dark blues/a little gold/yellow. Something that goes with our logo. We want our logo incorporated. Here is all the info you need:
Business name: RV Bone & Vitality Center
Location: 38517 North Willowmere Ave
Coral Springs, FL 33071
Phone: 954-218-4063
Fax: 954-582-7341
Email: info@myrvbonecare.example

Names: Lydia Vance, M.D.
Board Certified Hand and Upper Extremity Surgeon

Ebo Dansu, M.D.
Board Certified Hip & Knee Replacement/General Orthopaedic Surgeon

Can decide what you want to put on the back. Maybe a slogan:
Steady Hands. Stronger Steps

I am just going to upload our logo. The only thing is if we select you as the winning design, the location, and phone numbers may change. We will need your help to update that once fully solidified.

Industry/Entity Type

Medical

Contact Information for Business Card

Colors
0054AA
0677BA
7BADD7
CADEEF
E8F1F8
0094D4
00A9DD
6FCCEA
C7EBF8
E9F6FB

Requirements
Must have
• class, appeal,
Should not have
• We want to air on the side of masculine if we are looking at masculine vs. feminine feel. But we still want it classy, sophisticated, and something we will love

```html
<!DOCTYPE html>
<html lang="en">
<head>
<meta charset="utf-8">
<title>RV Bone &amp; Vitality Center – Business Card</title>
<link rel="stylesheet" href="https://fonts.googleapis.com/css2?family=Montserrat:wght@400;500;700&display=swap">
<style>
  :root {
    --navy: #1c2b57;
    --gold: #c9a264;
    --ink: #2e2e33;
    --muted: #6b6b72;
    --card: #ffffff;
    --stage: #2f3033;
  }
  * { box-sizing: border-box; margin: 0; padding: 0; }
  html, body {
    width: 1200px; height: 875px; overflow: hidden;
    background: var(--stage);
    font-family: "Montserrat", Arial, sans-serif;
  }
  .sheet {
    width: 1200px; height: 875px;
    display: flex; flex-direction: column; align-items: center; justify-content: center;
    gap: 25px;
  }
  .card {
    position: relative;
    width: 700px; height: 400px;
    background: var(--card);
    border-radius: 22px;
    overflow: hidden;
  }
  .brand {
    display: flex; align-items: center; gap: 10px;
    color: var(--navy);
    font-weight: 700;
    letter-spacing: 0.02em;
  }
  .brand-dot {
    width: 14px; height: 14px; border-radius: 50%;
    background: var(--navy);
    flex: none;
  }
  /* Front */
  .card-front .brand {
    position: absolute; left: 50%; top: 150px;
    transform: translateX(-50%);
    font-size: 26px; white-space: nowrap;
  }
  .card-front .brand-dot { width: 20px; height: 20px; }
  .slogan {
    position: absolute; left: 0; right: 0; top: 265px;
    text-align: center;
    font-size: 17px; font-weight: 400; letter-spacing: 0.04em;
    color: var(--muted);
  }
  /* Back */
  .card-back .brand {
    position: absolute; right: 44px; top: 70px;
    font-size: 20px; white-space: nowrap;
  }
  .person { position: absolute; left: 44px; top: 205px; }
  .person-name {
    font-size: 34px; font-weight: 700; color: var(--navy);
    letter-spacing: 0.01em;
  }
  .person-title {
    margin-top: 6px;
    font-size: 14.5px; font-weight: 400; color: var(--ink);
  }
  .contacts {
    position: absolute; left: 44px; top: 300px;
    list-style: none;
    font-size: 15px; color: var(--ink);
  }
  .contacts li { display: flex; align-items: center; gap: 10px; line-height: 26px; }
  .contacts svg { width: 15px; height: 15px; fill: var(--navy); flex: none; }
  .address {
    position: absolute; right: 44px; top: 300px;
    text-align: right; font-style: normal;
    font-size: 15px; line-height: 22px; color: var(--ink);
  }
  .address .practice { color: var(--navy); font-weight: 500; }
</style>
</head>
<body>
<main class="sheet">

  <section class="card card-front" aria-label="Business card front">
    <div class="brand"><span class="brand-dot"></span>RV Bone &amp; Vitality Center</div>
    <p class="slogan">Steady Hands. Stronger Steps</p>
  </section>

  <section class="card card-back" aria-label="Business card back">
    <div class="brand"><span class="brand-dot"></span>RV Bone &amp; Vitality Center</div>

    <div class="person">
      <h1 class="person-name">Ebo Dansu, M.D.</h1>
      <p class="person-title">Board Certified Hip &amp; Knee Replacement/General Orthopaedic Surgeon</p>
    </div>

    <ul class="contacts">
      <li>
        <svg viewBox="0 0 16 16" aria-hidden="true"><path d="M3.6 1.2l2.3 2.6-1.3 1.9c.9 2 2.6 3.8 4.7 4.7l1.9-1.3 2.6 2.3-1.3 2.6C7 13.5 2.5 9 1 3.4z"/></svg>
        <span>954-218-4063</span>
      </li>
      <li>
        <svg viewBox="0 0 16 16" aria-hidden="true"><path d="M4 1h8v4H4zM1 6h14v6h-3v3H4v-3H1zm4 4v4h6v-4z"/></svg>
        <span>954-582-7341</span>
      </li>
      <li>
        <svg viewBox="0 0 16 16" aria-hidden="true"><path d="M1 3h14v1.2L8 9 1 4.2zm0 2.6l7 4.8 7-4.8V13H1z"/></svg>
        <span>info@myrvbonecare.example</span>
      </li>
    </ul>

    <address class="address">
      <span class="practice">RV Bone &amp; Vitality Center</span><br>
      38517 North Willowmere Ave<br>
      Coral Springs, FL 33071
    </address>
  </section>

</main>
</body>
</html>
```